Business Card Design

We like to use greens as you will see in our logo (but not TOO much green). We are a Dental Clinic in a somewhat eccentric community. We do not like the dated sharp designs which we see many dentists use. We're looking for something bright and fresh while still maintaining the integrity of the profession. Elegance is not necessarily what we are going for... we need for the design to be "mature" but also up-lifting.

See our logo.
Updates

Project Deadline Extended
Reason: We have 5 designs which we like. But we'd like to see a few more before committing to a design.

Project Deadline Extended
Reason: We are awaiting revisions to this project. We are still welcoming designs while we wait to see if designers are able to provide to us the revisions we require in order to proceed with a selection.

Target Market(s)

Younger families - ages late 20's to early 40's

Industry/Entity Type

Business

Contact Information for Business Card

Corwel T. Banfry DDS 2730 W. Halvert Rd. Ste. 7 Royal Oak, MI 48391 (248)555-0174 FX (248)555-0189 info@BrightwellDentalCareMi.com BrigthwellDentalCareMi.com on the back of the card we need an appointment reminder (For____ Date___ Time____) with "If you are unable to keep your appointment, kindly give 48 hours notice" at the bottom. No use of teeth in the design. DOUBLE SIDED DESIGN

Requirements
Should not have
• The use of pictures of teeth

```html
<!DOCTYPE html>
<html lang="en">
<head>
<meta charset="utf-8">
<title>Brightwell Dental Care – Business Card</title>
<link href="https://fonts.googleapis.com/css2?family=Signika:wght@400;600&family=Tinos:ital,wght@0,700;1,400&family=Arimo&display=swap" rel="stylesheet">
<style>
  :root {
    --page-bg: #ecebe8;
    --card-bg: #ffffff;
    --card-edge: #d6d6d6;
    --brand-green: #2f7d16;
    --name-green: #3b8c1c;
    --dot-green: #3f9a28;
    --mark-green: #8fd14f;
    --ink: #2b2b2b;
    --ink-soft: #444444;
    --note-grey: #666666;
  }
  * { box-sizing: border-box; margin: 0; padding: 0; }
  html, body { width: 1200px; height: 1089px; overflow: hidden; }
  body { background: var(--page-bg); position: relative; font-family: "Signika", sans-serif; }

  .card {
    position: absolute; top: 88px; width: 496px; height: 870px;
    background: var(--card-bg); border: 1px solid var(--card-edge);
  }
  .card--front { left: 113px; }
  .card--back { left: 641px; }

  .brand { position: absolute; left: 0; right: 0; text-align: center; color: var(--brand-green); font-family: "Signika", sans-serif; font-weight: 600; }
  .brand__dot { display: block; margin: 0 auto 8px; border-radius: 50%; background: var(--mark-green); }
  .brand__name { display: block; line-height: 1; }
  .brand__sub { display: block; line-height: 1; letter-spacing: 1px; }

  .card--front .brand { top: 38px; }
  .card--front .brand__dot { width: 58px; height: 58px; }
  .card--front .brand__name { font-size: 84px; }
  .card--front .brand__sub { font-size: 44px; margin-top: 6px; }

  .card--back .brand { top: 50px; }
  .card--back .brand__dot { width: 50px; height: 50px; }
  .card--back .brand__name { font-size: 74px; }
  .card--back .brand__sub { font-size: 38px; margin-top: 4px; }

  .dentist-name {
    position: absolute; top: 524px; left: 0; right: 0; text-align: center;
    font-size: 33px; font-weight: 600; color: var(--name-green); letter-spacing: 0.5px;
  }
  .divider {
    position: absolute; left: 68px; right: 68px; height: 0;
    border-top: 5px dotted var(--dot-green);
  }
  .contact {
    position: absolute; left: 0; right: 0; text-align: center;
    font-size: 23px; color: var(--ink); line-height: 1.4;
  }
  .contact__line { display: flex; justify-content: center; align-items: center; gap: 6px; }
  .contact__line svg { width: 20px; height: 20px; flex: none; fill: var(--ink); }
  .contact--phones { top: 596px; line-height: 1.42; }
  .contact--address { top: 724px; }
  .contact--web { top: 814px; }

  .appt-title {
    position: absolute; top: 314px; left: 28px;
    font-family: "Tinos", serif; font-weight: 700; font-size: 28px; color: var(--name-green);
  }
  .appt-label {
    position: absolute; font-family: "Arimo", sans-serif; font-size: 18px; color: var(--ink-soft);
  }
  .rule { position: absolute; height: 0; border-top: 1px dotted var(--ink-soft); }
  .rule--solid { border-top-style: solid; }
  .box { position: absolute; border: 1.5px solid #6c6c6c; background: var(--card-bg); }
  .box--next { width: 116px; height: 25px; top: 502px; }
  .box--day { width: 55px; height: 33px; }

  .appt-note {
    position: absolute; top: 733px; left: 28px; right: 16px;
    font-family: "Tinos", serif; font-style: italic; font-size: 25px; line-height: 1.25; color: var(--note-grey);
  }
</style>
</head>
<body>

<section class="card card--front" aria-label="Card front">
  <div class="brand">
    <span class="brand__dot"></span>
    <span class="brand__name">Brightwell</span>
    <span class="brand__sub">DENTAL CARE</span>
  </div>

  <p class="dentist-name">Corwel T. Banfry DDS</p>
  <div class="divider" style="top:578px"></div>

  <div class="contact contact--phones">
    <p class="contact__line">
      <svg viewBox="0 0 24 24" aria-hidden="true"><path d="M6.6 10.8a15 15 0 0 0 6.6 6.6l2.2-2.2a1 1 0 0 1 1-.25 11.4 11.4 0 0 0 3.6.57 1 1 0 0 1 1 1V20a1 1 0 0 1-1 1A17 17 0 0 1 3 4a1 1 0 0 1 1-1h3.5a1 1 0 0 1 1 1c0 1.25.2 2.45.57 3.57a1 1 0 0 1-.25 1z"/></svg>
      248-555-0174
    </p>
    <p class="contact__line">
      <svg viewBox="0 0 24 24" aria-hidden="true"><path d="M7 3h10v5H7zM4 9h16a2 2 0 0 1 2 2v7h-4v3H6v-3H2v-7a2 2 0 0 1 2-2zm4 7v3h8v-3z"/></svg>
      248-555-0189
    </p>
    <p class="contact__line">
      <svg viewBox="0 0 24 24" aria-hidden="true"><path d="M2 8l10-6 10 6v12H2zm2 1.2V18h16V9.2l-8 5z"/></svg>
      info@BrightwellDentalCareMi.com
    </p>
  </div>
  <div class="divider" style="top:709px"></div>

  <div class="contact contact--address">
    <p class="contact__line">
      <svg viewBox="0 0 24 24" aria-hidden="true"><path d="M12 2a7 7 0 0 1 7 7c0 5-7 13-7 13S5 14 5 9a7 7 0 0 1 7-7zm0 4a3 3 0 1 0 0 6 3 3 0 0 0 0-6z"/></svg>
      2730 W. Halvert Rd. Ste.
    </p>
    <p>7 Royal Oak, MI 48391</p>
  </div>
  <div class="divider" style="top:799px"></div>

  <div class="contact contact--web">
    <p class="contact__line">
      <svg viewBox="0 0 24 24" aria-hidden="true"><path d="M12 2a10 10 0 1 0 0 20 10 10 0 0 0 0-20zm6.9 9h-3a15 15 0 0 0-1.3-5.6A8 8 0 0 1 18.9 11zM12 4.1c.9 1.3 1.7 3.6 1.9 6.9h-3.8c.2-3.3 1-5.6 1.9-6.9zM9.4 5.4A15 15 0 0 0 8.1 11h-3a8 8 0 0 1 4.3-5.6zM5.1 13h3a15 15 0 0 0 1.3 5.6A8 8 0 0 1 5.1 13zm6.9 6.9c-.9-1.3-1.7-3.6-1.9-6.9h3.8c-.2 3.3-1 5.6-1.9 6.9zm2.6-1.3a15 15 0 0 0 1.3-5.6h3a8 8 0 0 1-4.3 5.6z"/></svg>
      www.BrightwellDentalCareMi.com
    </p>
  </div>
</section>

<section class="card card--back" aria-label="Card back">
  <div class="brand">
    <span class="brand__dot"></span>
    <span class="brand__name">Brightwell</span>
    <span class="brand__sub">DENTAL CARE</span>
  </div>

  <h2 class="appt-title">YOUR APPOINTMENT</h2>

  <span class="appt-label" style="top:416px;left:28px">Name :</span>
  <div class="rule" style="top:433px;left:100px;width:356px"></div>

  <span class="appt-label" style="top:462px;left:28px">Date :</span>
  <div class="rule rule--solid" style="top:479px;left:84px;width:118px"></div>
  <span class="appt-label" style="top:462px;left:222px">Time :</span>
  <div class="rule rule--solid" style="top:479px;left:282px;width:110px"></div>
  <span class="appt-label" style="top:462px;left:393px">am / pm</span>

  <span class="appt-label" style="top:506px;left:28px">Next Appointment</span>
  <div class="box box--next" style="left:203px"></div>
  <div class="box box--next" style="left:357px"></div>

  <span class="appt-label" style="top:597px;left:28px">MON</span>
  <div class="box box--day" style="top:588px;left:101px"></div>
  <span class="appt-label" style="top:597px;left:174px">TUE</span>
  <div class="box box--day" style="top:588px;left:234px"></div>
  <span class="appt-label" style="top:597px;left:307px">WED</span>
  <div class="box box--day" style="top:588px;left:378px"></div>

  <span class="appt-label" style="top:648px;left:28px">THU</span>
  <div class="box box--day" style="top:639px;left:91px"></div>
  <span class="appt-label" style="top:648px;left:174px">FRI</span>
  <div class="box box--day" style="top:639px;left:226px"></div>
  <span class="appt-label" style="top:648px;left:307px">SAT</span>
  <div class="box box--day" style="top:639px;left:365px"></div>

  <p class="appt-note">If you are unable to keep your appointment, kindly give 48 hours notice</p>
</section>

</body>
</html>
```